Redesign Digital Lending Mobile App - Android/ Flutter

Want to re-theme an existing Digital Lending Mobile app to simplify customer journeys, as well as uplift the UI.

Most users will have small screen phones so the design needs to take that into consideration while also adapting to those with larger devices, like admins with Tablets.

Have already laid out customer journeys on Figma with guidance on how the flow of the app should be. https://www.plankora.example/board/q4ZtRm81KdWe7YhXcvBnaL/LoomKit?frame-id=3-5182&s=Jk2pQwEr7TyUi-9

Video capture of current app: https://vaultbin.example/clip/7Hx3LmQp9RtZw2KcVn4YsBd8EfGj1/play
https://vaultbin.example/clip/4PsWq8ZnTk2LrXy6MbJc3VhGd9FeA/play

The documented views for Web are also here https://docshelf.example/open?ref=3B8F2204AD7C91E5!tk8d1f6a2c4e7b90d3f5a1c8e2b6d4f9a07&cid=3b8f2204ad7c91e5&kind=file%2Cdocx&wdo=2

Target Market(s)

Kenya, Tanzania, Uganda - Africa

Industry/Entity Type

Fintech

Requirements
Must have
• Responsive for diff screens, esp. in context of smaller screen smartphone
Nice to have
• Thematic components to ensure new views can easily be adapted to these themse

```html
<!DOCTYPE html>
<html lang="en">
<head>
<meta charset="utf-8">
<title>LoomKit – Lending App Screens</title>
<link href="https://fonts.googleapis.com/css2?family=Plus+Jakarta+Sans:wght@400;500;600;700;800&display=swap" rel="stylesheet">
<style>
:root{
  --green:#48a068;
  --blue:#3a7bd0;
  --blue-deep:#2f6cc0;
  --sky:#dff0fa;
  --ink:#1c1c1c;
  --muted:#8c8c8c;
  --line:#444;
  --track:#e8e8e8;
  --pink:#e6197f;
  --lime:#99cc33;
  --white:#fff;
  --bg:#000;
}
*{box-sizing:border-box;margin:0;padding:0}
html,body{width:692px;height:1200px;overflow:hidden;background:var(--bg)}
body{font-family:"Plus Jakarta Sans",Arial,sans-serif;color:var(--ink)}
.stage{position:absolute;left:0;top:0;width:1456px;height:2525px;transform:scale(.47527);transform-origin:0 0}
.screen{position:absolute;background:var(--white);overflow:hidden}
.abs{position:absolute}

/* header */
.app-header{position:absolute;left:0;top:0;right:0;height:68px;display:flex;align-items:center;padding:0 14px;box-shadow:0 2px 6px rgba(0,0,0,.06)}
.brand{display:flex;align-items:center;gap:8px;font-weight:800;font-size:19px;color:var(--blue)}
.brand-dot{width:38px;height:38px;border-radius:50%;border:4px solid var(--blue)}
.header-icons{margin-left:auto;display:flex;gap:18px}
.header-icons svg{width:30px;height:30px;stroke:var(--blue);fill:none;stroke-width:1.8}

/* filter */
.filter{position:absolute;background:var(--green);padding:12px 16px;color:var(--white)}
.filter-title{font-size:16px;margin-bottom:9px}
.filter-row{display:flex;gap:11px}
.select{background:var(--white);color:var(--ink);font-size:12.5px;height:38px;display:flex;align-items:center;justify-content:space-between;padding:0 12px}
.select svg{width:12px;height:8px;stroke:var(--ink);fill:none;stroke-width:1.4}

/* search */
.search{position:absolute;border:1px solid var(--line);background:#f3f3f3;height:52px;display:flex;align-items:center;justify-content:space-between;padding:0 16px 0 26px;font-size:15px}
.search svg{width:18px;height:18px;stroke:var(--ink);fill:none;stroke-width:1.6}

/* table */
.details{position:absolute;border-collapse:collapse;font-size:15.5px}
.details td{border:1px solid var(--line);padding:0 22px}
.details td:last-child{padding-left:44px}

/* next */
.next{position:absolute;background:var(--green);color:var(--white);font-weight:600;font-size:24px;display:flex;align-items:center;justify-content:center;gap:14px}
.next svg{width:44px;height:16px;stroke:var(--white);fill:none;stroke-width:2.4}

/* nav */
.nav{position:absolute;left:0;right:0;bottom:0;background:var(--blue);display:flex;color:var(--white)}
.nav-item{flex:1;display:flex;flex-direction:column;align-items:center;justify-content:center;gap:6px;font-size:14px}
.nav-item.active{background:var(--green)}
.nav-item svg{width:30px;height:30px;stroke:var(--white);fill:none;stroke-width:1.5}

/* dashboard */
.stats{position:absolute;left:10px;top:89px;right:10px;display:flex;gap:8px}
.stat{flex:1;height:115px;background:var(--blue);color:var(--white);display:flex;flex-direction:column;align-items:center;justify-content:flex-end;padding-bottom:12px}
.stat svg{width:34px;height:34px;stroke:var(--white);fill:none;stroke-width:1.8;margin-bottom:8px}
.stat-value{font-size:18px;font-weight:600}
.stat-label{font-size:13.5px}
.metric{position:absolute;left:10px;right:22px;height:70px}
.metric-icon{position:absolute;left:0;top:0;width:66px;height:66px;border-radius:50%;border:2px solid var(--blue);display:flex;align-items:center;justify-content:center}
.metric-icon svg{width:34px;height:34px;stroke:var(--blue);fill:none;stroke-width:1.6}
.metric-name{position:absolute;left:88px;top:4px;font-size:17px}
.metric-amount{position:absolute;right:0;top:2px;font-size:17px}
.metric-track{position:absolute;left:90px;right:0;top:40px;height:15px;border-radius:8px;background:var(--track)}
.metric-fill{height:100%;border-radius:8px;background:var(--green)}
.section-title{position:absolute;left:15px;font-size:21px;font-weight:600}

/* finance */
.total{position:absolute;left:0;right:0;top:69px;height:120px;background:var(--sky);text-align:center;padding-top:26px}
.total-label{font-size:27px}
.total-value{font-size:34px;font-weight:700;color:var(--blue)}
.chips{position:absolute;left:23px;right:25px;top:236px;display:flex;gap:12px}
.chip{flex:1;height:37px;background:var(--blue);color:var(--white);font-size:14px;display:flex;align-items:center;justify-content:center}
.tabs{position:absolute;left:0;right:0;top:295px;height:44px;display:flex;font-size:21px;color:var(--white)}
.tabs div{flex:1;display:flex;align-items:center;justify-content:center}
.tab-profit{background:var(--green)}
.tab-loss{background:#262626}
.periods{position:absolute;left:0;right:0;top:339px;height:46px;display:flex;background:var(--sky);font-size:16px}
.periods div{flex:1;display:flex;align-items:center;justify-content:center}
.periods .on{background:var(--blue);color:var(--white)}
.money-grid{position:absolute;left:13px;right:13px;top:705px;display:grid;grid-template-columns:1fr 1fr;gap:12px}
.money{height:68px;background:var(--green);color:var(--white);display:flex;align-items:center;gap:14px;padding-left:20px}
.money svg{width:44px;height:44px;stroke:var(--white);fill:none;stroke-width:1.8}
.money-label{font-size:14.5px;line-height:1.1}
.money-value{font-size:20px;font-weight:600}
.axis text{font-size:6px;fill:#555;font-family:"Plus Jakarta Sans",Arial,sans-serif}
</style>
</head>
<body>
<svg width="0" height="0" style="position:absolute">
  <defs>
    <symbol id="i-user" viewBox="0 0 30 30"><circle cx="15" cy="15" r="13"/><circle cx="15" cy="12" r="5"/><path d="M6 24c3-5 15-5 18 0"/></symbol>
    <symbol id="i-bell" viewBox="0 0 30 30"><path d="M7 22V14a8 8 0 0 1 16 0v8l2 2H5z"/><path d="M12 26a3 3 0 0 0 6 0"/><path d="M15 3v3"/></symbol>
    <symbol id="i-home" viewBox="0 0 30 30"><path d="M4 14L15 4l11 10"/><path d="M7 12v14h6v-7h4v7h6V12"/></symbol>
    <symbol id="i-loans" viewBox="0 0 30 30"><rect x="9" y="4" width="12" height="4"/><rect x="9" y="9" width="12" height="4"/><rect x="9" y="14" width="12" height="4"/><path d="M3 24l6-4h8l4 2-8 1M21 22l6-3-2 6H3"/></symbol>
    <symbol id="i-summary" viewBox="0 0 30 30"><rect x="5" y="4" width="16" height="22"/><path d="M9 10h8M9 14h8M9 18h5"/><path d="M25 9l-8 12-2 4 4-2 8-12z"/></symbol>
    <symbol id="i-report" viewBox="0 0 30 30"><rect x="5" y="6" width="18" height="20"/><path d="M8 21l4-5 3 3 5-6"/><circle cx="20" cy="8" r="5"/></symbol>
    <symbol id="i-settings" viewBox="0 0 30 30"><circle cx="15" cy="15" r="4"/><path d="M13 3h4l1 4 3 1 3-2 3 3-2 3 1 3 4 1v4l-4 1-1 3 2 3-3 3-3-2-3 1-1 4h-4l-1-4-3-1-3 2-3-3 2-3-1-3-4-1v-4l4-1 1-3-2-3 3-3 3 2 3-1z"/></symbol>
    <symbol id="i-chev" viewBox="0 0 12 8"><path d="M1 1l5 5 5-5"/></symbol>
    <symbol id="i-search" viewBox="0 0 18 18"><circle cx="7.5" cy="7.5" r="6"/><path d="M12 12l5 5"/></symbol>
    <symbol id="i-arrow" viewBox="0 0 44 16"><path d="M0 8h42M34 1l8 7-8 7"/></symbol>
    <symbol id="i-cal" viewBox="0 0 34 34"><rect x="3" y="6" width="24" height="22" rx="2"/><path d="M3 12h24M9 3v6M21 3v6"/><circle cx="26" cy="26" r="6"/><path d="M26 23v3h2"/></symbol>
    <symbol id="i-coin" viewBox="0 0 34 34"><circle cx="20" cy="12" r="8"/><path d="M20 8v8M17 10h5M17 14h5"/><path d="M2 24h6l6 2h8l6-4-2 6-10 3H2"/></symbol>
    <symbol id="i-doc" viewBox="0 0 34 34"><rect x="6" y="4" width="20" height="26" rx="2"/><path d="M10 10h12M10 15h12M10 20h8"/><circle cx="25" cy="26" r="5"/><path d="M23 26l2 2 3-4"/></symbol>
    <symbol id="i-bag" viewBox="0 0 34 34"><path d="M8 14c-4 6-2 16 6 16s10-10 6-16z"/><path d="M10 10h8l-2 4h-4z"/><path d="M22 16h8M22 21h8M22 26h8"/></symbol>
    <symbol id="i-box" viewBox="0 0 34 34"><path d="M4 30h26M6 30V16h22v14"/><path d="M17 3v9M13 8l4 4 4-4"/><path d="M10 21h3M16 21h3M22 21h3"/></symbol>
    <symbol id="i-users" viewBox="0 0 34 34"><circle cx="14" cy="10" r="6"/><path d="M3 30c0-8 6-12 11-12s6 1 7 2"/><circle cx="25" cy="24" r="6"/><path d="M22 24l2 2 4-4"/></symbol>
    <symbol id="i-newuser" viewBox="0 0 34 34"><circle cx="17" cy="10" r="6"/><path d="M6 30c0-8 5-12 11-12s11 4 11 12"/><path d="M17 22v6M14 25h6"/></symbol>
    <symbol id="i-rev" viewBox="0 0 44 44"><circle cx="16" cy="14" r="10"/><path d="M16 8v12M13 11h5M13 17h5"/><path d="M4 40l12-10 6 5 16-12M32 23h6v6"/></symbol>
    <symbol id="i-exp" viewBox="0 0 44 44"><rect x="6" y="4" width="20" height="34" rx="2"/><path d="M12 12h8M16 8v8M10 24h12M10 30h6"/><circle cx="30" cy="30" r="8"/><path d="M30 26v8"/></symbol>
    <symbol id="i-tax" viewBox="0 0 44 44"><rect x="10" y="4" width="24" height="34" rx="2"/><path d="M14 10h16v6H14z"/><path d="M15 22h3M21 22h3M27 22h3M15 28h3M21 28h3M27 28h3"/><circle cx="10" cy="36" r="6"/></symbol>
    <symbol id="i-sal" viewBox="0 0 44 44"><circle cx="24" cy="12" r="8"/><path d="M24 8v8M21 10h5M21 14h5"/><path d="M4 30h8l8 3h8l10-6-2 7-14 5H4"/></symbol>
  </defs>
</svg>

<main class="stage">

  <!-- Loan details, compact -->
  <section class="screen" style="left:175px;top:178px;width:482px;height:959px">
    <header class="app-header">
      <div class="brand"><span class="brand-dot"></span>LoomKit</div>
      <div class="header-icons"><svg><use href="#i-user"/></svg><svg><use href="#i-bell"/></svg></div>
    </header>
    <div class="filter" style="left:5px;top:85px;width:471px;height:95px">
      <div class="filter-title">Filter by</div>
      <div class="filter-row">
        <div class="select" style="width:119px">Loan Officer<svg><use href="#i-chev"/></svg></div>
        <div class="select" style="width:90px">Branch<svg><use href="#i-chev"/></svg></div>
        <div class="select" style="width:88px">Fund<svg><use href="#i-chev"/></svg></div>
        <div class="select" style="width:114px">Product<svg><use href="#i-chev"/></svg></div>
      </div>
    </div>
    <div class="search" style="left:5px;top:203px;width:471px">Search<svg><use href="#i-search"/></svg></div>
    <table class="details" style="left:5px;top:282px;width:471px">
      <tr style="height:58px"><td style="width:256px">Loan reference number</td><td>3123</td></tr>
      <tr style="height:51px"><td>Loan status</td><td>Active</td></tr>
      <tr style="height:52px"><td>Date disbursed</td><td>July 13, 2024</td></tr>
      <tr style="height:54px"><td>Date approved</td><td>July 18, 2024</td></tr>
      <tr style="height:51px"><td>Last repayment date</td><td>July 25, 2024</td></tr>
      <tr style="height:53px"><td>Next repayment date</td><td>August 13, 2024</td></tr>
      <tr style="height:53px"><td>Amount disbursed</td><td>$25,000</td></tr>
      <tr style="height:55px"><td>Amount outstanding</td><td>$15,000</td></tr>
      <tr style="height:56px"><td>Overdue days</td><td>30</td></tr>
    </table>
    <div class="next" style="left:5px;top:791px;width:469px;height:57px">NEXT<svg><use href="#i-arrow"/></svg></div>
    <nav class="nav" style="height:85px">
      <div class="nav-item"><svg><use href="#i-home"/></svg>Home</div>
      <div class="nav-item active"><svg><use href="#i-loans"/></svg>Loans</div>
      <div class="nav-item" style="flex:1.15"><svg><use href="#i-summary"/></svg>Summary</div>
      <div class="nav-item"><svg><use href="#i-report"/></svg>Report</div>
      <div class="nav-item"><svg><use href="#i-settings"/></svg>Settings</div>
    </nav>
  </section>

  <!-- Dashboard -->
  <section class="screen" style="left:769px;top:153px;width:500px;height:1141px">
    <header class="app-header">
      <div class="brand"><span class="brand-dot"></span>LoomKit</div>
      <div class="header-icons"><svg><use href="#i-user"/></svg><svg><use href="#i-bell"/></svg></div>
    </header>
    <div class="stats">
      <div class="stat"><svg><use href="#i-bag"/></svg><div class="stat-value">$30,000</div><div class="stat-label">Disbursed</div></div>
      <div class="stat"><svg><use href="#i-box"/></svg><div class="stat-value">$20,000</div><div class="stat-label">Collected</div></div>
      <div class="stat"><svg><use href="#i-users"/></svg><div class="stat-value">50</div><div class="stat-label">Active Clients</div></div>
      <div class="stat"><svg><use href="#i-newuser"/></svg><div class="stat-value">1354</div><div class="stat-label">New Clients</div></div>
    </div>
    <div class="filter" style="left:8px;top:216px;width:480px;height:97px">
      <div class="filter-title">Filter by</div>
      <div class="filter-row">
        <div class="select" style="width:122px">Loan Officer<svg><use href="#i-chev"/></svg></div>
        <div class="select" style="width:91px">Branch<svg><use href="#i-chev"/></svg></div>
        <div class="select" style="width:91px">Fund<svg><use href="#i-chev"/></svg></div>
        <div class="select" style="width:116px">Product<svg><use href="#i-chev"/></svg></div>
      </div>
    </div>
    <div class="metric" style="top:340px"><div class="metric-icon"><svg><use href="#i-cal"/></svg></div><div class="metric-name">Near Due</div><div class="metric-amount">$25,00,000</div><div class="metric-track"><div class="metric-fill" style="width:58%"></div></div></div>
    <div class="metric" style="top:425px"><div class="metric-icon"><svg><use href="#i-cal"/></svg></div><div class="metric-name">Due</div><div class="metric-amount">$34,000</div><div class="metric-track"><div class="metric-fill" style="width:45%"></div></div></div>
    <div class="metric" style="top:512px"><div class="metric-icon"><svg><use href="#i-coin"/></svg></div><div class="metric-name">Pending Disbursement</div><div class="metric-amount">$39,000</div><div class="metric-track"><div class="metric-fill" style="width:38%"></div></div></div>
    <div class="metric" style="top:600px"><div class="metric-icon"><svg><use href="#i-doc"/></svg></div><div class="metric-name">Active Loans</div><div class="metric-amount">$25,000</div><div class="metric-track"><div class="metric-fill" style="width:27%"></div></div></div>
    <div class="section-title" style="top:695px">Reports</div>
    <svg class="abs axis" style="left:0;top:740px" width="500" height="190" viewBox="0 0 500 190">
      <g stroke="#ececec" stroke-width="1">
        <path d="M26 14h460M26 29.5h460M26 45h460M26 60.5h460M26 76h460M26 91.5h460M26 107h460M26 122.5h460M26 138h460M26 153.5h460M26 169h460"/>
        <path d="M26 14v155M63 14v155M101 14v155M139 14v155M177 14v155M215 14v155M253 14v155M291 14v155M329 14v155M367 14v155M405 14v155M443 14v155M481 14v155"/>
      </g>
      <g text-anchor="end"><text x="22" y="16">100</text><text x="22" y="31">90</text><text x="22" y="47">80</text><text x="22" y="62">70</text><text x="22" y="78">60</text><text x="22" y="93">50</text><text x="22" y="109">40</text><text x="22" y="124">30</text><text x="22" y="140">20</text><text x="22" y="155">10</text><text x="22" y="171">0</text></g>
      <g text-anchor="middle"><text x="44" y="182">JAN</text><text x="82" y="182">FEB</text><text x="120" y="182">MAR</text><text x="158" y="182">APR</text><text x="196" y="182">MAY</text><text x="234" y="182">JUN</text><text x="272" y="182">JUL</text><text x="310" y="182">AUG</text><text x="348" y="182">SEP</text><text x="386" y="182">OCT</text><text x="424" y="182">NOV</text><text x="462" y="182">DEC</text></g>
      <circle cx="414" cy="7" r="3" fill="var(--pink)"/><text x="419" y="9">Sales</text>
      <circle cx="452" cy="7" r="3" fill="var(--lime)"/><text x="457" y="9">Orders</text>
      <polyline fill="none" stroke="var(--lime)" stroke-width="1.3" points="26,107 63,93 101,107 139,62 177,62 215,77 253,62 291,62 329,37 367,29 405,29 443,36 481,29"/>
      <polyline fill="none" stroke="var(--pink)" stroke-width="1.3" points="26,154 63,124 101,139 139,92 177,77 215,108 253,93 291,108 329,77 367,47 405,62 443,77 481,47"/>
      <g fill="var(--lime)"><circle cx="26" cy="107" r="2.2"/><circle cx="63" cy="93" r="2.2"/><circle cx="101" cy="107" r="2.2"/><circle cx="139" cy="62" r="2.2"/><circle cx="177" cy="62" r="2.2"/><circle cx="215" cy="77" r="2.2"/><circle cx="253" cy="62" r="2.2"/><circle cx="291" cy="62" r="2.2"/><circle cx="329" cy="37" r="2.2"/><circle cx="367" cy="29" r="2.2"/><circle cx="405" cy="29" r="2.2"/><circle cx="443" cy="36" r="2.2"/><circle cx="481" cy="29" r="2.2"/></g>
      <g fill="var(--pink)"><circle cx="26" cy="154" r="2.2"/><circle cx="63" cy="124" r="2.2"/><circle cx="101" cy="139" r="2.2"/><circle cx="139" cy="92" r="2.2"/><circle cx="177" cy="77" r="2.2"/><circle cx="215" cy="108" r="2.2"/><circle cx="253" cy="93" r="2.2"/><circle cx="291" cy="108" r="2.2"/><circle cx="329" cy="77" r="2.2"/><circle cx="367" cy="47" r="2.2"/><circle cx="405" cy="62" r="2.2"/><circle cx="443" cy="77" r="2.2"/><circle cx="481" cy="47" r="2.2"/></g>
    </svg>
    <div class="next" style="left:16px;top:963px;width:461px;height:58px">NEXT<svg><use href="#i-arrow"/></svg></div>
    <nav class="nav" style="height:88px">
      <div class="nav-item active"><svg><use href="#i-home"/></svg>Home</div>
      <div class="nav-item"><svg><use href="#i-loans"/></svg>Loans</div>
      <div class="nav-item" style="flex:1.2"><svg><use href="#i-summary"/></svg>Summary</div>
      <div class="nav-item"><svg><use href="#i-report"/></svg>Report</div>
      <div class="nav-item"><svg><use href="#i-settings"/></svg>Settings</div>
    </nav>
  </section>

  <!-- Profit and loss -->
  <section class="screen" style="left:195px;top:1378px;width:500px;height:960px">
    <header class="app-header">
      <div class="brand"><span class="brand-dot"></span>LoomKit</div>
      <div class="header-icons"><svg><use href="#i-user"/></svg><svg><use href="#i-bell"/></svg></div>
    </header>
    <div class="total"><div class="total-label">Total Loan</div><div class="total-value">$35,00,000</div></div>
    <div class="abs" style="left:22px;top:206px;font-size:15.5px">Filter by</div>
    <div class="chips"><div class="chip">Loan officer</div><div class="chip">Branch</div><div class="chip">Fund</div><div class="chip">Product</div></div>
    <div class="tabs"><div class="tab-profit">Profit</div><div class="tab-loss">Loss</div></div>
    <div class="periods"><div>Day</div><div>Weak</div><div class="on">Month</div><div>Year</div></div>
    <svg class="abs axis" style="left:0;top:400px" width="500" height="285" viewBox="0 0 500 285">
      <g stroke="#ececec" stroke-width="1">
        <path d="M27 14h473M27 37.5h473M27 61h473M27 84.5h473M27 108h473M27 131.5h473M27 155h473M27 178.5h473M27 202h473M27 225.5h473M27 249h473"/>
        <path d="M27 14v235M83 14v235M141 14v235M199 14v235M257 14v235M315 14v235M372 14v235M430 14v235M488 14v235"/>
      </g>
      <g text-anchor="end"><text x="21" y="16">100</text><text x="21" y="40">90</text><text x="21" y="63">80</text><text x="21" y="87">70</text><text x="21" y="110">60</text><text x="21" y="134">50</text><text x="21" y="157">40</text><text x="21" y="181">30</text><text x="21" y="204">20</text><text x="21" y="228">10</text><text x="21" y="251">0</text></g>
      <polyline fill="none" stroke="var(--lime)" stroke-width="1.4" points="27,155 83,131.5 141,155 199,84.5 257,84.5 315,108 372,84.5 430,84.5 488,44.5 500,40"/>
      <g fill="var(--lime)"><circle cx="27" cy="155" r="3"/><circle cx="83" cy="131.5" r="3"/><circle cx="141" cy="155" r="3"/><circle cx="199" cy="84.5" r="3"/><circle cx="257" cy="84.5" r="3"/><circle cx="315" cy="108" r="3"/><circle cx="372" cy="84.5" r="3"/><circle cx="430" cy="84.5" r="3"/><circle cx="488" cy="44.5" r="3"/></g>
      <g style="font-size:16px" text-anchor="middle"><text x="58" y="276" style="font-size:16px">Week 1</text><text x="187" y="276" style="font-size:16px">Week 2</text><text x="315" y="276" style="font-size:16px">Week 3</text><text x="443" y="276" style="font-size:16px">Week 4</text></g>
    </svg>
    <div class="money-grid">
      <div class="money"><svg><use href="#i-rev"/></svg><div><div class="money-label">Revenue</div><div class="money-value">$300.00</div></div></div>
      <div class="money"><svg><use href="#i-exp"/></svg><div><div class="money-label">Expenses</div><div class="money-value">$350.00</div></div></div>
      <div class="money"><svg><use href="#i-tax"/></svg><div><div class="money-label">Tax</div><div class="money-value">$200.00</div></div></div>
      <div class="money"><svg><use href="#i-sal"/></svg><div><div class="money-label">Salaries</div><div class="money-value">$3500</div></div></div>
    </div>
    <nav class="nav" style="height:83px">
      <div class="nav-item"><svg><use href="#i-home"/></svg>Home</div>
      <div class="nav-item"><svg><use href="#i-loans"/></svg>Loans</div>
      <div class="nav-item" style="flex:1.2"><svg><use href="#i-summary"/></svg>Summary</div>
      <div class="nav-item active"><svg><use href="#i-report"/></svg>Report</div>
      <div class="nav-item"><svg><use href="#i-settings"/></svg>Settings</div>
    </nav>
  </section>

  <!-- Loan details, large -->
  <section class="screen" style="left:769px;top:1378px;width:500px;height:974px">
    <header class="app-header">
      <div class="brand"><span class="brand-dot"></span>LoomKit</div>
      <div class="header-icons"><svg><use href="#i-user"/></svg><svg><use href="#i-bell"/></svg></div>
    </header>
    <div class="filter" style="left:10px;top:86px;width:480px;height:97px">
      <div class="filter-title">Filter by</div>
      <div class="filter-row">
        <div class="select" style="width:122px">Loan Officer<svg><use href="#i-chev"/></svg></div>
        <div class="select" style="width:91px">Branch<svg><use href="#i-chev"/></svg></div>
        <div class="select" style="width:91px">Fund<svg><use href="#i-chev"/></svg></div>
        <div class="select" style="width:116px">Product<svg><use href="#i-chev"/></svg></div>
      </div>
    </div>
    <div class="search" style="left:10px;top:207px;width:480px;font-size:16px">Search<svg><use href="#i-search"/></svg></div>
    <table class="details" style="left:10px;top:287px;width:480px;font-size:16.5px">
      <tr style="height:60px"><td style="width:260px">Loan reference number</td><td>3123</td></tr>
      <tr style="height:51px"><td>Loan status</td><td>Active</td></tr>
      <tr style="height:53px"><td>Date disbursed</td><td>July 13, 2024</td></tr>
      <tr style="height:55px"><td>Date approved</td><td>July 18, 2024</td></tr>
      <tr style="height:52px"><td>Last repayment date</td><td>July 25, 2024</td></tr>
      <tr style="height:54px"><td>Next repayment date</td><td>August 13, 2024</td></tr>
      <tr style="height:54px"><td>Amount disbursed</td><td>$25,000</td></tr>
      <tr style="height:56px"><td>Amount outstanding</td><td>$15,000</td></tr>
      <tr style="height:57px"><td>Overdue days</td><td>30</td></tr>
    </table>
    <div class="next" style="left:10px;top:805px;width:478px;height:58px">NEXT<svg><use href="#i-arrow"/></svg></div>
    <nav class="nav" style="height:85px">
      <div class="nav-item"><svg><use href="#i-home"/></svg>Home</div>
      <div class="nav-item active"><svg><use href="#i-loans"/></svg>Loans</div>
      <div class="nav-item" style="flex:1.2"><svg><use href="#i-summary"/></svg>Summary</div>
      <div class="nav-item"><svg><use href="#i-report"/></svg>Report</div>
      <div class="nav-item"><svg><use href="#i-settings"/></svg>Settings</div>
    </nav>
  </section>

</main>
</body>
</html>
```